Zielgruppe
Ich bin Autor und arbeite derzeit an einem Projekt der Genres Humor / Action / Thriller.
Meine Zielgruppe sind männliche Leser zwischen 16 und 40 Jahren, die Action und Humor mögen. Es handelt sich um einen Teil einer Buchreihe, daher soll das Cover auf einem Vorgängercover aufbauen.
Aufgabenstellung
Allgemein:
- Das Cover soll sich am Erscheinungsbild des alten Covers orientieren (Dateien angefügt)
- Schriftart und -Position sollten gleich dem alten Cover sein, um einen Wiedererkennungswert zu haben (alte Fonts: Titel in Cooper Hewitt, Autorenname in Antonio)
- Mindestgröße in Pixeln: Höhe min. 2500 Pixel, Breite min. 1600 Pixel (oder größer in gleichem Seitenverhältnis)
- Grafiken / Bilder: Bitte von bildquell-demo.com
Gestaltung:
- Eher düster statt hell und freundlich
- Im Hintergrund sollte ein bedrohlich wirkendes Kernkraftwerk zu sehen sein
- Buchtitel: Spion Zander: Wirrwarr
- Sollte auch in Schwarzweiß und stark verkleinert noch gut lesbar sein

```html
<!DOCTYPE html>
<html lang="de">
<head>
<meta charset="utf-8">
<title>Spion Zander: Wirrwarr – Buchumschlag</title>
<link rel="stylesheet" href="https://fonts.googleapis.com/css2?family=Antonio:wght@300;400&family=Archivo:wght@800&display=swap">
<style>
  :root {
    --night: #0d1618;
    --night-deep: #05090b;
    --haze: #2a3634;
    --tower-navy: #060a1e;
    --sign-yellow: rgba(214, 168, 40, 0.95);
    --sign-rim: rgba(150, 90, 24, 0.85);
    --spine: #04080a;
    --paper-white: #ececec;
    --hazard-yellow: #d2a424;
    --copy-yellow: #d8a52a;
  }
  html, body {
    margin: 0;
    padding: 0;
    width: 1200px;
    height: 929px;
    overflow: hidden;
    background: var(--night-deep);
  }
  .cover {
    position: relative;
    width: 1200px;
    height: 929px;
    overflow: hidden;
  }
  .front {
    position: absolute;
    left: 0; top: 0;
    width: 595px;
    height: 929px;
    overflow: hidden;
  }
  .front-photo {
    position: absolute;
    inset: 0;
    background:
      radial-gradient(circle at 295px 537px, #fff3c8 0px, var(--sign-yellow) 14px, var(--sign-yellow) 96px, var(--sign-rim) 113px, rgba(6,10,30,0) 122px),
      radial-gradient(ellipse 210px 560px at 297px 640px, var(--tower-navy) 0%, var(--tower-navy) 70%, rgba(6,10,30,0) 100%),
      radial-gradient(ellipse at 25% 40%, var(--haze) 0%, var(--night) 55%, var(--night-deep) 100%);
  }
  .spine-shadow {
    position: absolute;
    left: 595px; top: 0;
    width: 11px;
    height: 929px;
    background: var(--spine);
  }
  .back {
    position: absolute;
    left: 606px; top: 0;
    width: 594px;
    height: 929px;
    background: radial-gradient(ellipse at 50% 42%, #1d2826 0%, var(--night) 58%, var(--night-deep) 100%);
  }
  .title {
    position: absolute;
    left: 0; top: 0;
  }
  .title text {
    font-family: "Archivo", "Work Sans", sans-serif;
    font-weight: 800;
  }
  .author {
    position: absolute;
    left: 0;
    width: 595px;
    top: 848px;
    margin: 0;
    text-align: center;
    font-family: "Antonio", sans-serif;
    font-weight: 400;
    font-size: 44px;
    line-height: 1;
    color: var(--paper-white);
  }
  .tagline {
    position: absolute;
    left: 68px;
    top: 56px;
    margin: 0;
    width: 510px;
    font-family: "Antonio", sans-serif;
    font-weight: 300;
    font-size: 41px;
    line-height: 50px;
    color: var(--paper-white);
  }
  .blurb {
    position: absolute;
    left: 68px;
    top: 187px;
    width: 458px;
    font-family: "Antonio", sans-serif;
    font-weight: 400;
    font-size: 18.4px;
    line-height: 31.5px;
    color: var(--copy-yellow);
  }
  .blurb p {
    margin: 0 0 31.5px 0;
    text-align: justify;
  }
</style>
</head>
<body>
<main class="cover">
  <section class="front">
    <div class="front-photo" role="img" aria-label="Fotografie: nächtliches Kernkraftwerk, dunkler Kühlturm mit gelbem Strahlenwarnzeichen unter wolkigem Himmel"></div>
    <svg class="title" width="595" height="240" viewBox="0 0 595 240" role="heading" aria-level="1">
      <text x="36" y="116" font-size="72" textLength="523" lengthAdjust="spacingAndGlyphs">
        <tspan fill="var(--paper-white)">SPION </tspan><tspan fill="var(--hazard-yellow)">ZANDER</tspan>
      </text>
      <text x="36" y="220" font-size="102" fill="var(--paper-white)" textLength="523" lengthAdjust="spacingAndGlyphs">WIRRWARR</text>
    </svg>
    <p class="author">Malte Kornfeld</p>
  </section>

  <div class="spine-shadow"></div>

  <section class="back">
    <h2 class="tagline">Ein etwas anderer Agententhriller, wie man ihn nicht alle Tage liest.</h2>
    <div class="blurb">
      <p>Um seinem gefährlichen Arbeitsumfeld aus dem Weg zu gehen, setzt Agent Zander auf Kreativität und Improvisation statt auf Wahrheitstreue und sorgfältige Missionsplanung. Anstatt in riskanten Geheimoperationen zu spionieren und sein Leben zu riskieren, entspannt er lieber mit leichten Mädchen in Wellness-Hotels weitab von jeglicher Gefahr.</p>
      <p>Doch eines Tages wird sein entspanntes Agentenleben durch die rücksichtslose Berichterstattung eines lokalen Fernsehsenders erschüttert und seine dubiose Arbeitsweise fliegt mit einem Schlag auf. Plötzlich wird er von seinen eigenen Arbeitskollegen als Landesverräter gejagt. Zu allem Überfluss möchte sein Vorgesetzter, der zugleich sein Schwiegervater ist, ihn tot sehen. Vorbelastet mit diesem gestörten Schwiegervater-Sohn-Verhältnis sucht sich Zander einen sicheren Zufluchtsort, wo ihm keine Vergeltung droht.</p>
      <p>Gäbe es da nur nicht all diese Drogenkartelle, Geheimdienste, Verschwörungen und attraktiven Agentinnen …</p>
    </div>
  </section>
</main>
</body>
</html>
```